Manufacturer Website with Home and Product page

We have this website, veltaro.com, but we need another one for the Canadian market. Canadians like to deal with Canadians so we need to gear it to that. It will be a simpler website than the current site.

We will need a design for two pages, one for the home page and one for a product page.

I synthesized all the brief information for the designers here, descriptions for both pages are included:

https://files.brimlodge.net/doc/8qwx3Lm2Rt7Yp0KzVb4Nc6HsJd9FgA1eUi5Tr

Supporting Folder:
https://files.brimlodge.net/folder/7ZpqW3nTx8Kd2LmR5vYb0HcJs

Industry/Entity Type

Tanning Beds, Red Light Beds, Hydro massage beds

Number of Pages Required

2 page

Requirements
Must have
• Two page descriptions: https://files.brimlodge.net/doc/8qwx3Lm2Rt7Yp0KzVb4Nc6HsJd9FgA1eUi5Tr/view
Nice to have
• Information Folder: https://files.brimlodge.net/folder/u/0/7ZpqW3nTx8Kd2LmR5vYb0HcJs

```html
<!DOCTYPE html>
<html lang="en">
<head>
<meta charset="utf-8">
<title>Veltaro Canada — Commercial Tanning, Red Light and Water Massage</title>
<link rel="stylesheet" href="https://fonts.googleapis.com/css2?family=Playfair+Display:ital,wght@1,700;1,800&family=Montserrat:ital,wght@0,400;0,500;0,600;1,800;1,900&display=swap">
<style>
:root{
  --brand:#6b79b8;
  --brand-soft:#7c89c4;
  --navy:#0c2a3a;
  --ink:#111;
  --muted:#555;
  --mist:#f3f4f9;
  --footer:#333333;
  --footer-base:#2a2a2a;
  --white:#fff;
  --maple:#d6202a;
}
*{box-sizing:border-box;margin:0;padding:0}
html,body{width:1200px;height:3747px;overflow:hidden}
body{position:relative;font-family:'Montserrat',sans-serif;color:var(--ink);background:var(--white)}
.abs{position:absolute}
.display{font-family:'Playfair Display',serif;font-style:italic;font-weight:800;text-transform:uppercase}

/* header */
.brand{left:0;top:0;width:368px;height:133px;background:var(--white);display:flex;align-items:center;justify-content:center;gap:10px;box-shadow:0 2px 8px rgba(0,0,0,.08);z-index:2}
.brand-name{font-family:'Montserrat',sans-serif;font-weight:600;font-size:46px;color:var(--brand);letter-spacing:1px}
.brand-mark{width:14px;height:14px;background:var(--maple)}
.topbar{left:368px;top:0;width:832px;height:45px;background:var(--brand);display:flex;align-items:center;gap:38px;padding-left:72px;font-size:11.5px;color:var(--white)}
.topbar .strong{font-weight:600;font-size:12px}
.topbar span{display:flex;align-items:center;gap:10px}
.mainnav{left:368px;top:45px;width:832px;height:88px;display:flex;align-items:center;justify-content:space-around;padding:0 40px;font-size:10.5px;color:#444;text-transform:uppercase}

/* hero */
.hero{left:0;top:133px;width:1200px;height:675px;background:var(--brand)}
.hero-frame{left:70px;top:200px;width:60px;height:505px;border-left:8px solid var(--white);border-top:8px solid var(--white);border-bottom:8px solid var(--white)}
.hero-photo{left:78px;top:208px;width:508px;height:489px;background:linear-gradient(135deg,#c9a0b8 0%,#e8c8cc 40%,#b8b0d6 70%,#8a85b8 100%)}
.dot{left:45px;width:12px;height:12px;border-radius:50%;background:#c7cce6}
.dot.on{background:var(--white);width:15px;height:15px;left:44px}
.hero-copy{right:88px;top:255px;width:560px;text-align:right;color:var(--white)}
.hero-kicker{font-size:18.5px;font-weight:500;letter-spacing:.5px}
.hero-title{font-size:42px;line-height:49px;margin-top:8px}
.hero-text{font-size:11.5px;line-height:28px;margin-top:10px}
.hero-actions{margin-top:28px;display:flex;justify-content:flex-end;gap:19px}
.btn{display:inline-flex;align-items:center;justify-content:center;height:37px;font-family:'Playfair Display',serif;font-style:italic;font-weight:700;font-size:11px;color:var(--white);text-transform:uppercase;letter-spacing:.5px}
.btn-dark{background:var(--navy);width:165px}
.btn-soft{background:var(--brand-soft);width:165px;border:1px solid #9aa4d4}

/* products */
.section-title{font-size:40px}
.product-photo{top:1000px;width:326px;height:388px}
.product-label{top:1388px;width:225px;height:75px;background:var(--brand);color:var(--white);display:flex;align-items:center;justify-content:center;font-family:'Playfair Display',serif;font-style:italic;font-weight:700;font-size:16.5px;text-transform:uppercase}

/* beauty */
.beauty{left:0;top:1552px;width:1200px;height:905px;background:var(--mist)}
.beauty-title{left:0;top:1640px;width:1200px;text-align:center}
.beauty-text{left:180px;top:1705px;width:840px;text-align:center;font-size:11.5px;line-height:28px;color:#333}
.beauty-frame{left:150px;top:2113px;width:899px;height:179px;border:8px solid var(--brand);border-top:none}
.beauty-photo{left:162px;top:1843px;width:875px;height:432px;background:linear-gradient(120deg,#e8dcd0 0%,#f2e6dc 35%,#d9b49a 60%,#efe7e0 100%)}
.arrow{top:2329px;width:36px;height:36px;border-radius:50%;display:flex;align-items:center;justify-content:center}
.arrow.prev{left:555px;background:var(--white);box-shadow:0 2px 6px rgba(0,0,0,.15)}
.arrow.next{left:608px;background:var(--brand)}

/* steps */
.step{width:295px;height:138px;background:var(--brand);border-radius:8px}
.step-card{position:absolute;left:8px;top:8px;width:284px;height:117px;background:var(--white);border-radius:6px;display:flex;align-items:center;padding-left:12px;gap:14px;box-shadow:0 2px 6px rgba(0,0,0,.08)}
.step-num{font-weight:900;font-style:italic;font-size:52px;width:70px}
.step-head{font-family:'Playfair Display',serif;font-style:italic;font-weight:700;font-size:11px;text-transform:uppercase}
.step-text{font-size:9px;line-height:15.5px;color:#555;margin-top:6px;width:170px}
.learn{left:517px;top:3003px;width:165px;height:37px}

/* footer */
.footer{left:0;top:3130px;width:1200px;height:580px;background:var(--footer);color:var(--white)}
.footer-brand{left:0;top:3230px;width:1200px;display:flex;align-items:center;justify-content:center;gap:10px}
.footer-brand .brand-name{font-size:52px}
.foot-head{font-family:'Playfair Display',serif;font-style:italic;font-weight:700;font-size:16px;text-transform:uppercase;color:var(--white)}
.foot-small{font-size:10.5px;line-height:17px;color:#ddd}
.foot-line{font-size:11.5px;color:#eee}
.foot-line b{font-weight:600;margin-right:12px}
.divider{top:3372px;width:1px;height:176px;background:#777}
.links{left:441px;top:3395px;width:314px;text-align:center;font-size:10.5px;line-height:22.5px;color:#ddd}
.social{top:3401px;width:23px;height:23px;border-radius:50%;background:var(--brand)}
.field{left:827px;top:3451px;width:225px;height:36px;background:var(--white);border:1px solid #ccc;font-size:8.5px;color:#555;display:flex;align-items:center;padding-left:14px}
.search{left:827px;top:3500px;width:165px;height:36px;background:var(--brand)}
.base{left:0;top:3710px;width:1200px;height:37px;background:var(--footer-base);color:#ddd;font-size:11px;display:flex;align-items:center;justify-content:center}
</style>
</head>
<body>

<header>
  <div class="abs brand"><span class="brand-name">Veltaro</span><span class="brand-mark"></span></div>
  <div class="abs topbar">
    <span><svg width="14" height="14" viewBox="0 0 24 24"><path fill="#fff" d="M6.6 10.8a15 15 0 0 0 6.6 6.6l2.2-2.2c.3-.3.7-.4 1-.2 1.1.4 2.3.6 3.6.6.6 0 1 .4 1 1V20c0 .6-.4 1-1 1A17 17 0 0 1 3 4c0-.6.4-1 1-1h3.5c.6 0 1 .4 1 1 0 1.3.2 2.5.6 3.6.1.3 0 .7-.2 1z"/></svg>555.010.2040</span>
    <span><svg width="16" height="12" viewBox="0 0 16 12"><rect width="16" height="12" rx="1" fill="#fff"/><path d="M1 1l7 5 7-5" stroke="#6b79b8" stroke-width="1.5" fill="none"/></svg>hello@northglowmail.com</span>
    <span class="strong">REQUEST A QUOTE</span>
    <span class="strong">REVENUE A CALCULATOR</span>
  </div>
  <nav class="abs mainnav">
    <span>Tanning</span><span>Massage</span><span>Red Light</span><span>Salon Startup</span><span>About Us</span><span>Contact Us</span>
  </nav>
</header>

<section>
  <div class="abs hero"></div>
  <div class="abs hero-frame"></div>
  <div class="abs hero-photo" role="img" aria-label="Photo of a woman relaxing in a commercial tanning bed wearing protective goggles"></div>
  <div class="abs dot on" style="top:413px"></div>
  <div class="abs dot" style="top:448px"></div>
  <div class="abs dot" style="top:480px"></div>
  <div class="abs hero-copy">
    <p class="hero-kicker">THE LEADING MANUFACTURER IN</p>
    <h1 class="display hero-title">Commercial Tanning,<br>Red Light and Water<br>Massage Therapy</h1>
    <p class="hero-text">Veltaro Is Dedicated To Providing Our Customers With The Highest Quality<br>Commercial Tanning And Wellness Equipment In The Business. We Pride<br>Ourselves On Our 35 Year History Of Legendary Customer Service And Support.<br>Whether You're Opening A Salon Or Looking For New Revenue Streams For An<br>Existing Salon, Spa, Or Fitness Center, Veltaro Has You Covered.</p>
    <div class="hero-actions"><span class="btn btn-dark">Request a Catalog</span><span class="btn btn-soft">View Our Products</span></div>
  </div>
</section>

<section>
  <h2 class="abs display section-title" style="left:120px;top:898px">Veltaro Products</h2>
  <div class="abs product-photo" style="left:120px;background:linear-gradient(160deg,#3a0505,#c81c14 55%,#5a0a08)" role="img" aria-label="Photo of a woman lying in a glowing red light therapy bed"></div>
  <div class="abs product-photo" style="left:469px;background:linear-gradient(160deg,#6c8a4a,#2a2a2a 40%,#d8c8c4 70%,#b84a5a)" role="img" aria-label="Photo of a woman relaxing on a hydro massage bed"></div>
  <div class="abs product-photo" style="left:817px;background:linear-gradient(160deg,#e6eef0,#c8d6da 40%,#2ab0c8 70%,#e8eef2)" role="img" aria-label="Photo of a woman in sunglasses and headphones on a poolside lounger"></div>
  <div class="abs product-label" style="left:170px">Red Light Bed</div>
  <div class="abs product-label" style="left:519px">Hydro Massage Bed</div>
  <div class="abs product-label" style="left:868px">Tanning Bed</div>
</section>

<section>
  <div class="abs beauty"></div>
  <h2 class="abs display section-title beauty-title">Beauty and Spa</h2>
  <p class="abs beauty-text">Distinguish Yourself As A Premier Industry Leader In Your Region By Providing An Array Of Our Exquisite Luxury Wellness Equipment. Enhance Your Spa Packages By Incorporating Our State-Of-The-Art LumaDerm Red Light Technology System And The Indulgent HydroVela Water Massage Therapy Bed. This Combination Guarantees That Every Guest Enjoys A Truly Immersive Experience Of Absolute Relaxation And Rejuvenation.</p>
  <div class="abs beauty-frame"></div>
  <div class="abs beauty-photo" role="img" aria-label="Photo of a woman receiving a relaxing back massage at a spa"></div>
  <div class="abs arrow prev"><svg width="14" height="10" viewBox="0 0 14 10"><path d="M13 5H2M5 1L1 5l4 4" stroke="#6b79b8" stroke-width="1.4" fill="none"/></svg></div>
  <div class="abs arrow next"><svg width="14" height="10" viewBox="0 0 14 10"><path d="M1 5h11M9 1l4 4-4 4" stroke="#fff" stroke-width="1.4" fill="none"/></svg></div>
</section>

<section>
  <h2 class="abs display section-title" style="left:120px;top:2548px">Starting a Salon or Spa?</h2>
  <div class="abs step" style="left:120px;top:2655px"><div class="step-card"><span class="step-num">01</span><div><p class="step-head">Develop a Business Plan</p><p class="step-text">Distinguish Yourself As A Premier Industry Leader In Your Region By Providing An Array Of Our Exquisite Luxury Wellness Equipment.</p></div></div></div>
  <div class="abs step" style="left:452px;top:2655px"><div class="step-card"><span class="step-num">02</span><div><p class="step-head">Space Design</p><p class="step-text">Distinguish Yourself As A Premier Industry Leader In Your Region By Providing An Array Of Our Exquisite Luxury Wellness Equipment.</p></div></div></div>
  <div class="abs step" style="left:782px;top:2655px"><div class="step-card"><span class="step-num">03</span><div><p class="step-head">Review Financing Options</p><p class="step-text">Distinguish Yourself As A Premier Industry Leader In Your Region By Providing An Array Of Our Exquisite Luxury Wellness Equipment.</p></div></div></div>
  <div class="abs step" style="left:452px;top:2826px"><div class="step-card"><span class="step-num">04</span><div><p class="step-head">Starup Marketing</p><p class="step-text">Distinguish Yourself As A Premier Industry Leader In Your Region By Providing An Array Of Our Exquisite Luxury Wellness Equipment.</p></div></div></div>
  <span class="abs btn btn-dark learn">Learn More</span>
</section>

<footer>
  <div class="abs footer"></div>
  <div class="abs footer-brand"><span class="brand-name">Veltaro</span><span class="brand-mark"></span></div>

  <h3 class="abs foot-head" style="left:147px;top:3342px">Veltaro International</h3>
  <p class="abs foot-small" style="left:147px;top:3374px;width:220px">1180 Harbour Lane North, Riverton,<br>FL 33900</p>
  <p class="abs foot-line" style="left:147px;top:3437px"><b>Sales:</b>555-014-0400</p>
  <p class="abs foot-line" style="left:147px;top:3467px"><b>Parts &amp; Services:</b>800.555.0185</p>
  <p class="abs foot-line" style="left:147px;top:3497px"><b>Main Line:</b>800.555.0176</p>

  <div class="abs divider" style="left:441px"></div>
  <h3 class="abs foot-head" style="left:441px;top:3342px;width:314px;text-align:center">Quick Links</h3>
  <div class="abs links">Commercial Tanning<br>Customer Service<br>Wellness Products<br>About Us<br>Replacement Lamps and Parts<br>Contact Veltaro<br>Salon Startup<br>Blog<br>Financing<br>Terms of Service<br>Privacy Policy</div>
  <div class="abs divider" style="left:755px"></div>

  <h3 class="abs foot-head" style="left:827px;top:3342px">Stay Connected</h3>
  <div class="abs social" style="left:827px"></div>
  <div class="abs social" style="left:866px"></div>
  <div class="abs social" style="left:905px"></div>
  <div class="abs social" style="left:944px"></div>
  <div class="abs social" style="left:983px"></div>
  <div class="abs social" style="left:1022px"></div>
  <div class="abs field">Let us help you find what you need</div>
  <span class="abs btn search">Search</span>

  <div class="abs base">© 2023 Veltaro International. All Rights Reserved</div>
</footer>

</body>
</html>
```